Veranix - Solution provider in business consulting

Veranix is a swiss based company providing solutions for developing markets. The business covers various fields of business consulting, such as supply chain, product costs, quality management and manufacturing management. The Business operates in a efficient, straight and solution oriented manner.
The final design should communicate these characteristics. Asian people as well as as western people shall identify the qualities of the company at first sight.
The customer needs business cards with a simple view but an recognizable design, printed in high quality. Engraved elements such as the globe or simple words are possible.
Available colors are: (RAL)
102/102/102
51/102/102
153/204/153
255/102/51
Font: Calibri

```html
<!DOCTYPE html>
<html lang="en">
<head>
<meta charset="utf-8">
<title>Veranix business cards</title>
<link href="https://fonts.googleapis.com/css2?family=Open+Sans:wght@300;400;600&display=swap" rel="stylesheet">
<style>
  :root {
    --stage: #ecebea;
    --card-white: #ffffff;
    --graphite: #666666;
    --ink: #1e1e1e;
  }
  * { margin: 0; padding: 0; box-sizing: border-box; }
  html, body { width: 1200px; height: 900px; overflow: hidden; }
  body {
    background: var(--stage);
    font-family: "Open Sans", sans-serif;
    position: relative;
  }
  .card {
    position: absolute;
    overflow: hidden;
  }
  .card-front {
    left: 78px; top: 35px;
    width: 588px; height: 363px;
    background: var(--card-white);
  }
  .card-back {
    left: 388px; top: 505px;
    width: 566px; height: 352px;
    background: var(--graphite);
  }
  .globe-art {
    position: absolute;
    left: 0; top: 0;
    width: 100%; height: 100%;
  }
  .wordmark {
    position: absolute;
    color: var(--card-white);
    font-weight: 300;
    line-height: 1;
    white-space: nowrap;
  }
  .card-front .wordmark { left: 36px; top: 48px; font-size: 48px; }
  .card-back .wordmark { left: 252px; top: 128px; font-size: 44px; }

  .identity {
    position: absolute;
    right: 36px; top: 62px;
    text-align: right;
    color: var(--graphite);
  }
  .identity .person-name { font-size: 20px; font-weight: 600; line-height: 1.1; }
  .identity .person-role { font-size: 15px; color: var(--ink); padding-right: 2px; }

  .contact-list {
    position: absolute;
    right: 36px; top: 143px;
    list-style: none;
    color: var(--ink);
    font-size: 15px;
  }
  .contact-list li {
    display: flex;
    justify-content: flex-end;
    align-items: center;
    gap: 8px;
    height: 25px;
  }
  .contact-list svg { width: 13px; height: 13px; fill: var(--graphite); flex: none; }

  .address {
    position: absolute;
    right: 36px; top: 257px;
    text-align: right;
    color: var(--ink);
    font-size: 15px;
    line-height: 22px;
    font-style: normal;
  }
</style>
</head>
<body>

<section class="card card-front">
  <svg class="globe-art" viewBox="0 0 588 363" role="img" aria-label="Globe illustration showing Asia and the Indian Ocean">
    <path d="M0 0 H258 C285 35 320 80 336 135 C345 175 320 215 290 245 C265 270 235 300 200 300 C150 300 110 290 0 262 Z" fill="var(--graphite)"/>
    <path d="M0 270 C50 320 120 352 210 363 H0 Z" fill="var(--graphite)"/>
  </svg>
  <div class="wordmark">Veranix</div>

  <div class="identity">
    <div class="person-name">Marco Feller</div>
    <div class="person-role">CEO</div>
  </div>

  <ul class="contact-list">
    <li>+41 79 385 2207
      <svg viewBox="0 0 16 16"><path d="M4 0h8a1.5 1.5 0 0 1 1.5 1.5v13A1.5 1.5 0 0 1 12 16H4a1.5 1.5 0 0 1-1.5-1.5v-13A1.5 1.5 0 0 1 4 0zm0 2v10.5h8V2zm4 11.2a.9.9 0 1 0 0 1.8.9.9 0 0 0 0-1.8z"/></svg>
    </li>
    <li>+41 71 840 3618
      <svg viewBox="0 0 16 16"><path d="M3.6 1 6 3.8 4.6 5.6a10 10 0 0 0 5.8 5.8l1.8-1.4L15 12.4 13.4 15C7 14.7 1.3 9 1 2.6z"/></svg>
    </li>
    <li>marco.feller@veranix.ch
      <svg viewBox="0 0 16 16"><path d="M1 3h14v10H1zm1.5 1.3v.3L8 8.6l5.5-4v-.3zm0 2v5.4h11V6.3L8 10.3z"/></svg>
    </li>
    <li>www.veranix.ch
      <svg viewBox="0 0 16 16"><path d="M8 1a7 7 0 1 0 0 14A7 7 0 0 0 8 1zm-1 2.2v2.3L5 7.5 3.3 6.6A5.2 5.2 0 0 1 7 3.2zm2.5.1a5.2 5.2 0 0 1 3.6 6.5l-1.9-1.5V6.5L10.4 5zM5.5 9.5 7.5 11v1.8a5.2 5.2 0 0 1-3.6-3.1z"/></svg>
    </li>
  </ul>

  <address class="address">
    Veranix GmbH Lindenweg 14<br>
    9247 Talberg Switzerland
  </address>
</section>

<section class="card card-back">
  <svg class="globe-art" viewBox="0 0 566 352" role="img" aria-label="Globe illustration showing Asia and the Indian Ocean">
    <path d="M0 0 H85 C60 60 20 110 0 120 Z M0 0 V352 H215 C265 330 310 300 338 268 C250 250 200 240 150 260 C110 270 60 240 0 200 Z" fill="var(--card-white)"/>
    <path d="M0 120 C20 110 60 60 85 0 H0 Z" fill="var(--card-white)"/>
  </svg>
  <div class="wordmark">Veranix</div>
</section>

</body>
</html>
```